Cool business cards

Use my existing logo from mark meadow (see images I have uploaded) and design a really cool non-stuffy business card. I am a divorce mediator.

```html
<!DOCTYPE html>
<html lang="en">
<head>
<meta charset="utf-8">
<title>Dana Whitfield, J.D. — Business Card</title>
<link rel="stylesheet" href="https://fonts.googleapis.com/css2?family=Montserrat:wght@600;700&family=Open+Sans:wght@400;700&display=swap">
<style>
  :root {
    --backdrop: #000000;
    --card: #ffffff;
    --card-edge: #d9d9d9;
    --brand-blue: #1565b0;
    --brand-orange: #f0821e;
    --ink-grey: #8c8c8c;
    --label-grey: #939393;
    --tagline-grey: #8a8a8a;
  }
  html, body {
    margin: 0;
    padding: 0;
    width: 1200px;
    height: 989px;
    overflow: hidden;
    background: var(--backdrop);
  }
  .canvas {
    position: relative;
    width: 1200px;
    height: 989px;
  }
  .card {
    position: absolute;
    left: 246px;
    width: 705px;
    height: 402px;
    background: var(--card);
    box-shadow: 0 0 0 1px var(--card-edge);
  }
  .card--front { top: 69px; }
  .card--back { top: 514px; }

  .brand {
    position: absolute;
    display: flex;
    flex-direction: column;
    align-items: center;
  }
  .brand__dot {
    border-radius: 50%;
    background: var(--brand-blue);
  }
  .brand__name {
    font-family: "Montserrat", sans-serif;
    font-weight: 700;
    color: var(--brand-blue);
    letter-spacing: 0.5px;
    white-space: nowrap;
    line-height: 1.1;
  }
  .brand__tagline {
    display: flex;
    align-items: center;
    font-family: "Montserrat", sans-serif;
    font-weight: 600;
    color: var(--tagline-grey);
    letter-spacing: 0.4px;
    white-space: nowrap;
    line-height: 1;
  }
  .brand__tagline::before,
  .brand__tagline::after {
    content: "";
    display: block;
    height: 1px;
    background: var(--tagline-grey);
  }

  .card--front .brand {
    left: 0; right: 0; top: 106px;
  }
  .card--front .brand__dot { width: 114px; height: 114px; }
  .card--front .brand__name { font-size: 23px; margin-top: 22px; }
  .card--front .brand__tagline { font-size: 11px; margin-top: 6px; }
  .card--front .brand__tagline::before,
  .card--front .brand__tagline::after { width: 22px; }
  .card--front .brand__tagline::before { margin-right: 8px; }
  .card--front .brand__tagline::after { margin-left: 8px; }

  .card--back .brand {
    left: 56px; width: 236px; top: 132px;
  }
  .card--back .brand__dot { width: 94px; height: 94px; }
  .card--back .brand__name { font-size: 19px; margin-top: 15px; }
  .card--back .brand__tagline { font-size: 9px; margin-top: 5px; }
  .card--back .brand__tagline::before,
  .card--back .brand__tagline::after { width: 18px; }
  .card--back .brand__tagline::before { margin-right: 6px; }
  .card--back .brand__tagline::after { margin-left: 6px; }

  .holder-name {
    position: absolute;
    left: 374px;
    top: 54px;
    margin: 0;
    font-family: "Open Sans", sans-serif;
    font-weight: 700;
    font-size: 20px;
    color: var(--label-grey);
  }
  .contact-list {
    position: absolute;
    left: 370px;
    top: 206px;
    margin: 0;
    padding: 0;
    list-style: none;
  }
  .contact-list__item {
    display: flex;
    align-items: center;
    height: 42px;
    font-family: "Open Sans", sans-serif;
    font-size: 20px;
    color: var(--ink-grey);
  }
  .contact-list__icon {
    width: 24px;
    height: 24px;
    margin-right: 10px;
    fill: var(--ink-grey);
  }
</style>
</head>
<body>
<main class="canvas">
  <section class="card card--front" aria-label="Card front">
    <div class="brand">
      <div class="brand__dot"></div>
      <div class="brand__name">DANA WHITFIELD, J.D.</div>
      <div class="brand__tagline">DIVORCE &amp; FAMILY MEDIATION</div>
    </div>
  </section>

  <section class="card card--back" aria-label="Card back">
    <div class="brand">
      <div class="brand__dot"></div>
      <div class="brand__name">DANA WHITFIELD, J.D.</div>
      <div class="brand__tagline">DIVORCE &amp; FAMILY MEDIATION</div>
    </div>

    <h2 class="holder-name">NAME</h2>

    <ul class="contact-list">
      <li class="contact-list__item">
        <svg class="contact-list__icon" viewBox="0 0 24 24" aria-hidden="true">
          <path d="M6.6 10.8c1.4 2.8 3.8 5.1 6.6 6.6l2.2-2.2c.3-.3.7-.4 1-.2 1.1.4 2.3.6 3.6.6.6 0 1 .4 1 1V20c0 .6-.4 1-1 1C10.6 21 3 13.4 3 4c0-.6.4-1 1-1h3.5c.6 0 1 .4 1 1 0 1.3.2 2.5.6 3.6.1.3 0 .7-.2 1L6.6 10.8z"/>
        </svg>
        +00 000000000
      </li>
      <li class="contact-list__item">
        <svg class="contact-list__icon" viewBox="0 0 24 24" aria-hidden="true">
          <path d="M2 5h20v14H2z M3.5 6.5v.4l8.5 6 8.5-6v-.4z" fill-rule="evenodd"/>
        </svg>
        name@danawhitfield.com
      </li>
      <li class="contact-list__item">
        <svg class="contact-list__icon" viewBox="0 0 24 24" aria-hidden="true">
          <g fill="none" stroke="#8c8c8c" stroke-width="1.6">
            <circle cx="12" cy="12" r="10"/>
            <ellipse cx="12" cy="12" rx="4.5" ry="10"/>
            <path d="M2 12h20M4 7h16M4 17h16"/>
          </g>
        </svg>
        www.danawhitfield.com
      </li>
    </ul>
  </section>
</main>
</body>
</html>
```